Wordpress Design Project for Employee Communications Site

We need a Wordpress design for a company that strategizes on and produces materials for employee communications. Improving employee communications at all levels of an organization can help improve overall company performance and results. The site needs to look very clean and professional; we're not afraid of white space. We like the functionality that Wordpress provides; however, we only want one "true" blog page; the other pages should give the impression of a more "static" web site - particularly the home page. I have a logo that I can provide.

I have added these comments to the discussion page:
Great question - thank you for asking it. I’ve done more research

I like the very clean and monochromatic looks to many of these. I don’t have to have monochromatic, but I do like minimal colors. Simple, clean, organized. The home page should “fit” almost entirely without scrolling. I do like fat footers that you can scroll down to. I don’t want a colored background, but any that I’ve chosen with colored backgrounds could be switched to a white background.

http://www.mirabelquennet.example/
http://pondraft.example/
http://v1.samplumworth.example/
http://howdythegoat.example/
http://stayingbrisk.example/
http://www.interiors.kelmun.example/
http://trelvmasters.example/

These last two are more corporate sites. The first one is from a well-respected consultant in my area who does a lot of what I do. And I think Harwenby does a nice job with their site. So, I want to marry the look I like with getting the content job done.

http://www.messagefuelbox.example/
http://www.harwenby.example/view/en_US/us/index.htm

Target Market(s)

Target market is mid- to large-sized companies. More than 500 employees.

Industry/Entity Type

Communications

Requirements
Must have
• Need an impactful home page. There should be a "blog" page; contact us; services; about. For starters, at least. I want fonts to be very readable - that is, either quite dark gray or black.
Nice to have
• I am loathe to include a picture of myself, but I do want some images that say, "professional" and "expert" in communications.
Should not have
• I don't want a hits counter :) (I know no one would do that!).

```html
<!DOCTYPE html>
<html lang="en">
<head>
<meta charset="utf-8">
<title>Brightwell Communications Group</title>
<link href="https://fonts.googleapis.com/css2?family=Ubuntu:wght@300;400;500&display=swap" rel="stylesheet">
<style>
:root{
  --sky:#03a8e4;
  --lime:#8ebc0c;
  --lime-dark:#6f9a05;
  --teal-heading:#1b8db5;
  --ink:#333;
  --body-text:#7b7b7b;
  --line:#e2e2e2;
  --panel:#f4f4f4;
  --footer:#efefef;
}
*{box-sizing:border-box;margin:0;padding:0}
html,body{width:1168px;height:1200px;overflow:hidden}
body{position:relative;background:#fff;font-family:"Ubuntu",sans-serif;color:var(--ink)}
.top-band{position:absolute;left:0;top:0;width:1168px;height:13px;background:var(--sky)}
.masthead{position:absolute;left:0;top:13px;width:1168px;height:152px;background:linear-gradient(#f7f7f7,#f1f1f1);border-bottom:1px solid #e4e4e4}
.brand{position:absolute;left:84px;top:38px;display:flex;align-items:center;gap:14px}
.brand-mark{width:58px;height:58px;border-radius:50%;background:var(--lime)}
.brand-name{font-weight:300;font-size:40px;color:var(--lime);line-height:1}
.brand-tag{position:absolute;left:156px;top:88px;font-weight:300;font-size:16px;color:var(--lime)}
.search{position:absolute;left:897px;top:37px;width:175px;height:25px;background:#fff;border:1px solid #d5d5d5;border-radius:2px;font-size:11px;color:#aaa;font-style:italic;padding:5px 0 0 17px}
.search svg{position:absolute;right:6px;top:6px}
.main-nav{position:absolute;top:111px;left:0;width:1168px;font-size:14px;color:#333}
.main-nav a{position:absolute;color:inherit;text-decoration:none}
.main-nav .current{color:var(--lime)}
.main-nav .current::after{content:"";position:absolute;left:-2px;right:-2px;top:22px;height:4px;background:var(--lime)}
.showcase{position:absolute;left:84px;top:188px;width:1001px;height:304px;background:#fff;box-shadow:0 6px 10px rgba(0,0,0,.06)}
.showcase-photo{position:absolute;left:11px;top:11px;width:980px;height:283px;background:linear-gradient(180deg,#8fbde8 0%,#b9d6f0 55%,#d7e6f3 100%)}
.showcase-title{position:absolute;left:47px;top:35px;font-family:"Ubuntu",sans-serif;font-weight:300;color:#2a2a2a;text-shadow:0 1px 0 rgba(255,255,255,.6)}
.showcase-title .line1{font-size:35px;display:block}
.showcase-title .line2{font-size:30px;display:block;margin-top:4px}
.slide-arrow{position:absolute;top:135px;width:28px;height:36px;background:rgba(255,255,255,.75);border-radius:3px}
.slide-arrow svg{position:absolute;left:8px;top:11px}
.slide-prev{left:0}
.slide-next{right:0}
.intro{position:absolute;left:96px;top:540px;width:624px}
.intro h1{font-weight:300;font-size:29px;color:var(--teal-heading)}
.intro h1 span{color:var(--lime)}
.intro p{margin-top:22px;font-size:12.4px;line-height:21.3px;color:var(--body-text);text-align:justify}
.features{position:absolute;left:96px;top:785px;width:624px}
.features h2{font-weight:300;font-size:22px;color:var(--lime)}
.feature{position:absolute;left:0;width:624px}
.feature-art{position:absolute;left:0;top:0;width:100px;height:70px;border-radius:6px}
.feature-art.globe{background:radial-gradient(circle at 50% 35%,#5fb3ea 0 22px,transparent 23px),linear-gradient(90deg,#d94b4b,#f2b233,#4caf50,#3d7fd6)}
.feature-art.team{background:radial-gradient(ellipse at 50% 75%,#f4d23c 0 20px,#3fa0e0 21px 30px,transparent 31px),#e9e9e9}
.feature p{position:absolute;left:137px;top:0;width:487px;font-size:12.4px;line-height:21.3px;color:var(--body-text);text-align:justify}
.btn-more{position:absolute;left:621px;top:1051px;width:98px;height:31px;border-radius:6px;background:linear-gradient(#a3cf1c,var(--lime-dark));color:#2f4a00;font-size:13px;text-align:center;line-height:31px;box-shadow:0 2px 2px rgba(0,0,0,.2)}
.sidebar{position:absolute;left:770px;top:517px;width:313px;height:577px;background:linear-gradient(90deg,#ececec,#fafafa 30%,#fff)}
.sidebar-head{position:absolute;left:757px;top:535px;width:302px;height:52px;background:linear-gradient(#9ccd12,#80ad08);border:1px solid #79a30a}
.sidebar-head::after{content:"";position:absolute;left:-1px;bottom:-9px;border-top:9px solid #5a7a04;border-left:13px solid transparent}
.sidebar-icon{position:absolute;left:25px;top:8px;width:36px;height:36px;border-radius:50%;background:#fff;border:3px solid #dcdcdc}
.sidebar-icon::before{content:"";position:absolute;inset:3px;border-radius:50%;background:var(--sky)}
.sidebar-icon svg{position:absolute;left:8px;top:8px}
.sidebar-head h3{position:absolute;left:72px;top:12px;font-weight:400;font-size:22px;color:#fff}
.post{position:absolute;left:787px;width:272px}
.post h4{font-weight:400;font-size:14px;color:var(--lime-dark);padding-left:27px;position:relative}
.post h4 svg{position:absolute;left:0;top:0}
.post .meta{margin-top:6px;font-size:11px;font-style:italic;color:#555}
.post p{margin-top:12px;font-size:11.7px;line-height:21.3px;color:var(--body-text);text-align:justify}
.post .more{display:block;text-align:right;font-size:12px;color:#555;margin-top:7px}
.post .rule{margin-top:10px;border-top:2px dotted #c9c9c9}
.footer{position:absolute;left:84px;top:1123px;width:1001px;height:68px;background:var(--footer)}
.footer-nav{position:absolute;left:20px;top:14px;font-size:12px;color:#333}
.footer-nav span{margin:0 8px;color:#666}
.footer-copy{position:absolute;left:20px;top:40px;font-size:12px;color:#333}
.social{position:absolute;right:34px;top:21px;display:flex;gap:12px}
.social i{display:block;width:26px;height:26px;border-radius:50%}
.social .s1{background:#3b5b9a}
.social .s2{background:#2fb6ea}
.social .s3{background:#1a84b8}
</style>
</head>
<body>
<div class="top-band"></div>
<header class="masthead">
  <div class="brand"><span class="brand-mark"></span><span class="brand-name">Brightwell</span></div>
  <div class="brand-tag">Brightwell Communications Group</div>
  <div class="search">Search
    <svg width="11" height="11" viewBox="0 0 11 11"><circle cx="4.5" cy="4.5" r="3.3" fill="none" stroke="#aaa" stroke-width="1.3"/><line x1="7" y1="7" x2="10" y2="10" stroke="#aaa" stroke-width="1.5"/></svg>
  </div>
</header>
<nav class="main-nav">
  <a class="current" style="left:557px">HOME</a>
  <a style="left:656px">ABOUT US</a>
  <a style="left:780px">SERVICES</a>
  <a style="left:897px">BLOG</a>
  <a style="left:992px">CONTACT US</a>
</nav>

<section class="showcase">
  <div class="showcase-photo" role="img" aria-label="Photograph of three smiling business professionals in suits against a bright blue sky">
    <div class="showcase-title"><span class="line1">Expressing professional</span><span class="line2">&amp; Expert in communication</span></div>
  </div>
  <div class="slide-arrow slide-prev" style="left:11px;top:146px"><svg width="10" height="14" viewBox="0 0 10 14"><polyline points="8,1 2,7 8,13" fill="none" stroke="#999" stroke-width="2.5"/></svg></div>
  <div class="slide-arrow slide-next" style="right:11px;top:146px"><svg width="10" height="14" viewBox="0 0 10 14"><polyline points="2,1 8,7 2,13" fill="none" stroke="#999" stroke-width="2.5"/></svg></div>
</section>

<section class="intro">
  <h1>Welcome to <span>Brightwell</span></h1>
  <p>Sed ut perspiciatis unde omnis iste natus error sit voluptatem accusantium doloremque laudantium, totam rem aperiam, eaque ipsa quae ab illo inventore veritatis et quasi architecto beatae vitae dicta sunt explicabo. Nemo enim ipsam voluptatem quia voluptas sit aspernatur aut odit aut fugit, sed quia consequuntur magni dolores eos qui ratione voluptatem sequi nesciunt. Neque porro quisquam est, qui dolorem ipsum quia dolor sit amet, consectetur, adipisci velit, sed quia non numquam eius modi tempora incidunt ut labore et dolore magnam aliquam quaerat voluptatem. Ut enim ad minima veniam, quis nostrum exercitationem ullam corporis suscipit laboriosam, nisi ut aliquid ex ea commodi consequatur.</p>
</section>

<section class="features">
  <h2>At vero eos et accusamus et iusto odio dignissimos</h2>
  <div class="feature" style="top:63px">
    <div class="feature-art globe" role="img" aria-label="Illustration of colourful figures standing around a globe"></div>
    <p>Quis autem vel eum iure reprehenderit qui in ea voluptate velit esse quam nihil molestiae consequatur, vel illum qui dolorem eum fugiat quo voluptas nulla pariatur. To take a trivial example, which of us ever undertakes laborious physical exercise, except to obtain some advantage from it.</p>
  </div>
  <div class="feature" style="top:180px">
    <div class="feature-art team" role="img" aria-label="Illustration of business silhouettes shaking hands on puzzle pieces"></div>
    <p>Quis autem vel eum iure reprehenderit qui in ea voluptate velit esse quam nihil molestiae consequatur, vel illum qui dolorem eum fugiat quo voluptas nulla pariatur. To take a trivial example, which of us ever undertakes laborious physical exercise, except to obtain some advantage from it.</p>
  </div>
</section>
<div class="btn-more">View more</div>

<aside class="sidebar"></aside>
<div class="sidebar-head">
  <div class="sidebar-icon"><svg width="14" height="14" viewBox="0 0 14 14"><rect x="1" y="1" width="9" height="9" fill="none" stroke="#fff" stroke-width="1.6"/><rect x="4" y="4" width="9" height="9" fill="none" stroke="#fff" stroke-width="1.6"/></svg></div>
  <h3>Blog Posts</h3>
</div>

<article class="post" style="top:616px">
  <h4><svg width="19" height="18" viewBox="0 0 19 18"><rect x="1" y="3" width="14" height="14" fill="none" stroke="#aaa" stroke-width="1.4"/><line x1="7" y1="11" x2="17" y2="1" stroke="#aaa" stroke-width="2"/></svg>Aoluptate velit nihil molestiae</h4>
  <div class="meta">Posted by : Martin on Jan 25<sup>th</sup></div>
  <p>Nemo enim ipsam voluptatem quia voluptas sit aspernatur aut odit aut fugit, sed quia dolores eos qui ratione</p>
  <span class="more">View more</span>
  <div class="rule"></div>
</article>
<article class="post" style="top:787px">
  <h4><svg width="19" height="18" viewBox="0 0 19 18"><rect x="1" y="3" width="14" height="14" fill="none" stroke="#aaa" stroke-width="1.4"/><line x1="7" y1="11" x2="17" y2="1" stroke="#aaa" stroke-width="2"/></svg>Aoluptate velit nihil molestiae</h4>
  <div class="meta">Posted by : Martin on Jan 25<sup>th</sup></div>
  <p>Nemo enim ipsam voluptatem quia voluptas sit aspernatur aut odit aut fugit, sed quia dolores eos qui ratione</p>
  <span class="more">View more</span>
  <div class="rule"></div>
</article>
<article class="post" style="top:958px">
  <h4><svg width="19" height="18" viewBox="0 0 19 18"><rect x="1" y="3" width="14" height="14" fill="none" stroke="#aaa" stroke-width="1.4"/><line x1="7" y1="11" x2="17" y2="1" stroke="#aaa" stroke-width="2"/></svg>Aoluptate velit nihil molestiae</h4>
  <div class="meta">Posted by : Martin on Jan 25<sup>th</sup></div>
  <p>Nemo enim ipsam voluptatem quia voluptas sit aspernatur aut odit aut fugit.</p>
  <span class="more">View more</span>
</article>

<footer class="footer">
  <div class="footer-nav">Home<span>|</span>About us<span>|</span>Services<span>|</span>Blog<span>|</span>Contact us.</div>
  <div class="footer-copy">Copyright © 2012 &nbsp; www.brightwell.example &nbsp; All rights reserved.</div>
  <div class="social"><i class="s1"></i><i class="s2"></i><i class="s3"></i></div>
</footer>
</body>
</html>
```